Spy/Espionage/Counterintelligence Membership Community Needs a PowerPoint Template

We need a powerpoint template for one of our business verticals focused on spies, espionage, and counterintelligence. The name of it is "Brass Lantern Guild" and the logo is attached. Brass Lantern Guild is a community that connects people with experts in espionage and counterintelligence through an online social network, as well as in-person events. We would like to see designs that incorporate the red and black of the logo. The design should communicate mystery/suspense and peak curiosity.

Target Market(s)

Late 20s to baby boomers, male

Industry/Entity Type

Social Club

Font styles to use
Sans Serif

Colors
ec1f27
000000
ffffff

Requirements
Must have
• A user-friendly ppt template file. Incorporate basic fonts that don't have to be installed on every computer for presentations. A cover slide and a basic inside slide. A white background. I will also need graphic source files.
Nice to have
• Plenty of space for slide title and body content. Logo on every slide.
Should not have
• Inconsistency with fonts. Misalignment of images.

```html
<!DOCTYPE html>
<html lang="en">
<head>
<meta charset="utf-8">
<title>Brass Lantern Guild – Our Services</title>
<link href="https://fonts.googleapis.com/css2?family=PT+Sans+Narrow:wght@400;700&family=Lato:ital,wght@0,400;1,400&display=swap" rel="stylesheet">
<style>
  :root {
    --brand-red: #ec1f27;
    --title-red: #a3101a;
    --bar-red-dark: #8e0b12;
    --bar-red: #c8141c;
    --ink: #000000;
    --text: #1c1c1c;
    --paper: #ffffff;
    --paper-shade: #eeeeee;
  }
  html, body {
    margin: 0;
    padding: 0;
    width: 1200px;
    height: 900px;
    overflow: hidden;
  }
  .slide {
    position: relative;
    width: 1200px;
    height: 900px;
    overflow: hidden;
    background: radial-gradient(ellipse at 40% 40%, var(--paper) 0%, #f6f6f6 60%, var(--paper-shade) 100%);
    font-family: "PT Sans Narrow", "Arial Narrow", sans-serif;
  }
  .title-tab {
    position: absolute;
    left: 0;
    top: 33px;
    width: 46px;
    height: 55px;
  }
  .slide-title {
    position: absolute;
    left: 60px;
    top: 26px;
    margin: 0;
    font-size: 50px;
    font-weight: 700;
    color: var(--title-red);
    letter-spacing: -0.5px;
  }
  .section-heading {
    position: absolute;
    left: 88px;
    top: 144px;
    margin: 0;
    font-size: 35px;
    font-weight: 700;
    color: var(--title-red);
  }
  .service-list {
    position: absolute;
    left: 92px;
    top: 206px;
    margin: 0;
    padding: 0;
    list-style: none;
  }
  .service-list li {
    display: flex;
    align-items: center;
    height: 39px;
    font-size: 25px;
    color: var(--text);
  }
  .service-list svg {
    width: 28px;
    height: 28px;
    margin-right: 15px;
    flex: none;
  }
  .team-photo {
    position: absolute;
    left: 428px;
    top: 195px;
    width: 712px;
    height: 555px;
    background: linear-gradient(180deg, #5a5350 0%, #3e3a3a 45%, #8c8580 70%, rgba(240,240,240,0.4) 100%);
    border-radius: 6px;
  }
  .brand-name {
    position: absolute;
    right: 16px;
    top: 748px;
    margin: 0;
    font-size: 44px;
    font-weight: 400;
    color: var(--ink);
    letter-spacing: -0.5px;
  }
  .footer-bar {
    position: absolute;
    left: 0;
    bottom: 0;
    width: 1200px;
    height: 90px;
    border-top: 5px solid var(--ink);
    box-sizing: border-box;
    background: linear-gradient(180deg, var(--bar-red) 0%, var(--bar-red-dark) 100%);
  }
  .page-number {
    position: absolute;
    left: 33px;
    top: 15px;
    width: 60px;
    height: 55px;
    background: var(--ink);
    border: 2px solid #5a5a5a;
    box-sizing: border-box;
    border-radius: 4px;
    color: var(--paper);
    font-family: "Lato", sans-serif;
    font-size: 30px;
    display: flex;
    align-items: center;
    justify-content: center;
  }
  .tagline {
    position: absolute;
    left: 129px;
    top: 24px;
    margin: 0;
    color: var(--paper);
    font-family: "Lato", sans-serif;
    font-style: italic;
    font-size: 26px;
  }
  .nav-button {
    position: absolute;
    top: 15px;
    width: 98px;
    height: 56px;
  }
  .nav-button svg { position: absolute; inset: 0; }
  .nav-button span {
    position: relative;
    display: flex;
    align-items: center;
    justify-content: center;
    height: 100%;
    color: var(--paper);
    font-family: "Lato", sans-serif;
    font-size: 23px;
  }
  .nav-back { left: 957px; }
  .nav-next { left: 1073px; }
</style>
</head>
<body>
<div class="slide">
  <svg class="title-tab" viewBox="0 0 46 55" aria-hidden="true">
    <polygon points="0,0 46,0 32,27.5 46,55 0,55" fill="var(--brand-red)"/>
  </svg>
  <h1 class="slide-title">Presentation Title</h1>

  <h2 class="section-heading">Our Services</h2>
  <ul class="service-list">
    <li><svg viewBox="0 0 28 28" aria-hidden="true"><rect x="2" y="6" width="18" height="18" fill="none" stroke="#444" stroke-width="2"/><path d="M6 14 L11 20 L25 3" fill="none" stroke="var(--title-red)" stroke-width="4"/></svg>Handymen</li>
    <li><svg viewBox="0 0 28 28" aria-hidden="true"><rect x="2" y="6" width="18" height="18" fill="none" stroke="#444" stroke-width="2"/><path d="M6 14 L11 20 L25 3" fill="none" stroke="var(--title-red)" stroke-width="4"/></svg>Contractors</li>
    <li><svg viewBox="0 0 28 28" aria-hidden="true"><rect x="2" y="6" width="18" height="18" fill="none" stroke="#444" stroke-width="2"/><path d="M6 14 L11 20 L25 3" fill="none" stroke="var(--title-red)" stroke-width="4"/></svg>Stagers</li>
    <li><svg viewBox="0 0 28 28" aria-hidden="true"><rect x="2" y="6" width="18" height="18" fill="none" stroke="#444" stroke-width="2"/><path d="M6 14 L11 20 L25 3" fill="none" stroke="var(--title-red)" stroke-width="4"/></svg>Painters</li>
    <li><svg viewBox="0 0 28 28" aria-hidden="true"><rect x="2" y="6" width="18" height="18" fill="none" stroke="#444" stroke-width="2"/><path d="M6 14 L11 20 L25 3" fill="none" stroke="var(--title-red)" stroke-width="4"/></svg>Cleaners</li>
    <li><svg viewBox="0 0 28 28" aria-hidden="true"><rect x="2" y="6" width="18" height="18" fill="none" stroke="#444" stroke-width="2"/><path d="M6 14 L11 20 L25 3" fill="none" stroke="var(--title-red)" stroke-width="4"/></svg>Movers</li>
    <li><svg viewBox="0 0 28 28" aria-hidden="true"><rect x="2" y="6" width="18" height="18" fill="none" stroke="#444" stroke-width="2"/><path d="M6 14 L11 20 L25 3" fill="none" stroke="var(--title-red)" stroke-width="4"/></svg>Storage companies</li>
    <li><svg viewBox="0 0 28 28" aria-hidden="true"><rect x="2" y="6" width="18" height="18" fill="none" stroke="#444" stroke-width="2"/><path d="M6 14 L11 20 L25 3" fill="none" stroke="var(--title-red)" stroke-width="4"/></svg>Landscapers</li>
    <li><svg viewBox="0 0 28 28" aria-hidden="true"><rect x="2" y="6" width="18" height="18" fill="none" stroke="#444" stroke-width="2"/><path d="M6 14 L11 20 L25 3" fill="none" stroke="var(--title-red)" stroke-width="4"/></svg>Estate Sale Professionals</li>
    <li><svg viewBox="0 0 28 28" aria-hidden="true"><rect x="2" y="6" width="18" height="18" fill="none" stroke="#444" stroke-width="2"/><path d="M6 14 L11 20 L25 3" fill="none" stroke="var(--title-red)" stroke-width="4"/></svg>Lawyers</li>
    <li><svg viewBox="0 0 28 28" aria-hidden="true"><rect x="2" y="6" width="18" height="18" fill="none" stroke="#444" stroke-width="2"/><path d="M6 14 L11 20 L25 3" fill="none" stroke="var(--title-red)" stroke-width="4"/></svg>Mortgage Brokers</li>
    <li><svg viewBox="0 0 28 28" aria-hidden="true"><rect x="2" y="6" width="18" height="18" fill="none" stroke="#444" stroke-width="2"/><path d="M6 14 L11 20 L25 3" fill="none" stroke="var(--title-red)" stroke-width="4"/></svg>Inspectors</li>
  </ul>

  <div class="team-photo" role="img" aria-label="Photo of a large group of business professionals and workers in suits and hard hats standing together on a reflective floor"></div>

  <p class="brand-name">Brass Lantern Guild</p>

  <footer class="footer-bar">
    <div class="page-number">04</div>
    <p class="tagline">tagline/slogan about your company</p>
    <a class="nav-button nav-back">
      <svg viewBox="0 0 98 56" aria-hidden="true"><polygon points="14,1 97,1 97,55 14,55 1,28" fill="var(--ink)" stroke="#555" stroke-width="1.5"/></svg>
      <span>Back</span>
    </a>
    <a class="nav-button nav-next">
      <svg viewBox="0 0 98 56" aria-hidden="true"><polygon points="1,1 84,1 97,28 84,55 1,55" fill="var(--ink)" stroke="#555" stroke-width="1.5"/></svg>
      <span>Next</span>
    </a>
  </footer>
</div>
</body>
</html>
```